Business card for a new innovative and professional lawn care business

We need a business card design for a new lawn care business in Halifax NS Canada. We offer lawn services in Halifax & Bedford. Our services offered include lawn care, garden services, and property maintenance. We take pride in our work and are experienced at what we do. I would like to see a design that is double sided. On the backside I would like the something simple (maybe my logo preferably on blackround (linked below) with website link, Facebook page or something). The front I want to include contact info:
Morgan Pell
phone 902-555-0148
email - brookvaleyards.ca
facebook - Facebook.com/brookvaleyards
Instagram maybe ? - instagram.com/brookvaleyard
Serving Halifax and Bedford for 5 years?
I don't want it to have too much information as I will be passing them out in aim to visit website, or call !
We do want it to include lawn care, garden services and property maintenance.
Basic, catchy, and modern looking !
Logo attached below !

Target Market(s)

Passing business cards to everyone I meet or interact with.

Industry/Entity Type

Lawn Care

Contact Information for Business Card

Double sided with some basic information, with catchy colours and easy to look at.

Font styles to use
Sans Serif

Requirements
Must have
• Must be double sided and have :
• Name, Phone, Email, FB, Website, and 3 main services offered - lawn care, property maintenance, garden services
Nice to have
• Would be nice to have instagram link if it goes well on there
Should not have
• Don't want too much writing or images that are distracting

```html
<!DOCTYPE html>
<html lang="en">
<head>
<meta charset="utf-8">
<title>Brookvale Yards – Business Card</title>
<link rel="stylesheet" href="https://fonts.googleapis.com/css2?family=Open+Sans:wght@400;600;700&display=swap">
<style>
  :root {
    --backdrop: #3a3330;
    --card: #141414;
    --green: #2f9e44;
    --lime: #7cc242;
    --text: #e8e8e8;
    --divider: #8a8a8a;
  }
  * { margin: 0; padding: 0; box-sizing: border-box; }
  html, body {
    width: 1200px; height: 814px; overflow: hidden;
    background: var(--backdrop);
    font-family: "Open Sans", Arial, sans-serif;
  }
  .canvas {
    width: 1200px; height: 814px;
    display: flex; align-items: center; justify-content: center; gap: 40px;
  }
  .card {
    width: 520px; height: 298px;
    background: var(--card);
    border-radius: 4px;
    box-shadow: 0 10px 30px rgba(0,0,0,.45);
    position: relative;
    color: var(--text);
  }
  /* contact side */
  .card--contact { display: flex; align-items: center; }
  .brand {
    display: flex; align-items: center; gap: 10px;
    font-weight: 700; color: var(--lime);
    letter-spacing: .02em;
  }
  .brand__dot {
    width: 14px; height: 14px; border-radius: 50%; background: var(--green); flex: none;
  }
  .card--contact .brand { width: 270px; padding-left: 36px; font-size: 26px; }
  .divider { width: 1px; height: 150px; background: var(--divider); }
  .contact { padding-left: 24px; }
  .contact__name { color: var(--green); font-weight: 600; font-size: 18px; margin-bottom: 6px; }
  .contact__list { list-style: none; }
  .contact__item {
    display: flex; align-items: center; gap: 8px;
    font-size: 13.5px; line-height: 21px;
  }
  .contact__icon { width: 11px; height: 11px; flex: none; fill: var(--green); }
  /* logo side */
  .card--logo {
    display: flex; flex-direction: column; align-items: center; justify-content: center; gap: 38px;
  }
  .card--logo .brand { font-size: 38px; }
  .card--logo .brand__dot { width: 18px; height: 18px; }
  .services {
    display: flex; align-items: center; gap: 7px;
    font-size: 13px; color: var(--text);
  }
  .services__tick { width: 12px; height: 12px; fill: none; stroke: var(--lime); stroke-width: 3; stroke-linecap: round; stroke-linejoin: round; }
</style>
</head>
<body>
<main class="canvas">
  <section class="card card--contact">
    <div class="brand"><span class="brand__dot"></span>Brookvale Yards</div>
    <div class="divider"></div>
    <div class="contact">
      <p class="contact__name">Morgan Pell</p>
      <ul class="contact__list">
        <li class="contact__item">
          <svg class="contact__icon" viewBox="0 0 24 24"><path d="M6.6 10.8a15.1 15.1 0 0 0 6.6 6.6l2.2-2.2a1 1 0 0 1 1-.25 11.4 11.4 0 0 0 3.6.57 1 1 0 0 1 1 1V20a1 1 0 0 1-1 1A17 17 0 0 1 3 4a1 1 0 0 1 1-1h3.5a1 1 0 0 1 1 1c0 1.25.2 2.45.57 3.57a1 1 0 0 1-.25 1z"/></svg>
          902-555-0148
        </li>
        <li class="contact__item">
          <svg class="contact__icon" viewBox="0 0 24 24"><path d="M2 5h20v14H2z M2 5l10 8 10-8" /></svg>
          info@brookvaleyards.ca
        </li>
        <li class="contact__item">
          <svg class="contact__icon" viewBox="0 0 24 24"><circle cx="12" cy="12" r="10"/></svg>
          brookvaleyards.ca
        </li>
        <li class="contact__item">
          <svg class="contact__icon" viewBox="0 0 24 24"><rect x="2" y="2" width="20" height="20" rx="3"/></svg>
          brookvaleyards
        </li>
        <li class="contact__item">
          <svg class="contact__icon" viewBox="0 0 24 24"><rect x="2" y="2" width="20" height="20" rx="3"/></svg>
          brookvaleyard
        </li>
      </ul>
    </div>
  </section>

  <section class="card card--logo">
    <div class="brand"><span class="brand__dot"></span>Brookvale Yards</div>
    <p class="services">
      <span>Lawn Care</span>
      <svg class="services__tick" viewBox="0 0 12 12"><path d="M2 6.5l2.5 2.5L10 3"/></svg>
      <span>Property Maintenance</span>
      <svg class="services__tick" viewBox="0 0 12 12"><path d="M2 6.5l2.5 2.5L10 3"/></svg>
      <span>Garden Services</span>
    </p>
  </section>
</main>
</body>
</html>
```